Design a cool print brochure for an NGO / Give your work a global impact!!

Hi,
I provide a full design brief (below, please scroll) and a mood board (attached) to help you visualize inside my head.. ;-)
I am also available to help and have worked many years in advertising; we will understand each other.
Objective:
To design an A4 folded in two presentation brochure for a non-profit consulting agency called Verdomo.
Verdomo works in sustainability and international development = working with NGO’s, governments and private sector on global issues such as global warming, education for all etc.
Strategy:
This document is a first step in developing a communication strategy. It will be distributed during a major international event called the Brightwater Aid Forum.
Objective:
The double objective of the brochure is:
a) to inform the recipient of what Verdomo is, in the shortest time possible.
b) to showcase relevant projects to demonstrate Verdomo experience and expertise.
Target:
Main target:
Existing Verdomo contacts, such as members of development organizations, NGOs, private sector foundations (CSR), regional networks and other development actors.
NB: the main target already has a certain awareness of Verdomo: we will try to minimize text to maximize visual impact and readability.
Secondary target:
Verdomo will also distribute the brochure to new prospects of interest during the Brightwater Forum.
Timing:
We will need to finalize the design and have the files by June 1st to allow time for print before the event.
Content:
The document should be concise, highly readable (no clutter) and include:
1. text (that we will provide)
and
2. visual elements such as images, shapes and info-graphics (that is you).
NB: Verdomo does not have its own image bank; photos will be provided by you.
Format:
A4 folded in half - 4pp A5 - PORTRAIT FORMAT) with an impactful visual in the front, logo, title and headline (please see examples in the mood board attached).
Design elements:
Verdomo does not have yet a visual identity (please see: http://verdomo.org) so there is room for creativity and no graphic chart to follow.
The sector of consulting in international development is rather conservative but our intention is to be disruptive and create a “Wow” effect. We count on you for that!
Therefore, the design should be “structured”, “organized”, “uncluttered” but also “modern”, “impactful”, “highly visual” (think infographic or mind map to describe our services and projects).
Please, take the time to see the attached presentation: I give you guidelines and examples of what we want and what we like.
We are looking forward to seeing your work and I am available for comments, questions and support.
Thank you.
RK
Target Market(s)
The full brief is in the project description: please, scroll through it.
The target market is : our existing clients base, working in sustainable development (read: NGO and Allied Assembly people)
Industry/Entity Type
Ngo
Font styles to use
Requirements
Must have
- - Design and color elements: please, no black and white. Our company website is in black and white and without graphics; we want the brochure to break away from that and start creating our brand identity; so please, show us colors and desing elements (shapes, backgrounds, etc).
- You have a chance to showcase your talent in terms of visual identity: what lines, forms, layout and colors can you come up with and apply throughout the brochure and serve as the visual identity of Verdomo?
- The structure of the document should be:
- - Front cover: design elements + impacful photo (see mood board example attached) +our logo + this headline: "Collective action for sustainable development and impact"
- - Inside front: a graphic representation of "Our Services": such as core activity in the center circle and satellite circles for the services we offer.
- - Inside back:
- 1. Icons and text boxes for "Our projects"
- 2. A world map of the countries where we have worked. Full list of countries is here:
- http://verdomo.org/experience-1
- - Back cover: our contact + logos of partners.
- Our partners are listed here:
- Please use their original logos (ie, in color).
- The design we will select will serve as a basis for a graphic chart...so more work to come...word to the wise ;)
- Please check out our website verdomo.org to see what we do etc.
Nice to have
- Icons to reflect our services: what icons can you come up with to describe "training services", "building networks" or "program management"?
- I give examples in the mood board.
Should not have
- We are open to creativity and want to generate a "Wow" effect.
- Just note that the sector is rather conservative so flashy colors and cartoon like characters should be avoided. Think "earth, global change, Allied Assembly, climate" without going too green (it's overdone). ;-)
- Make us stand out in the NGO world
- Now you.

```html
<!DOCTYPE html>
<html lang="en">
<head>
<meta charset="utf-8">
<title>Verdomo brochure</title>
<link href="https://fonts.googleapis.com/css2?family=Source+Sans+3:wght@400;600;700&display=swap" rel="stylesheet">
<style>
:root{
  --bg:#d3d4d6;
  --navy:#3e4f6d;
  --navy-dark:#26286b;
  --orange:#f29a2e;
  --text:#3a3f4a;
  --logo-grey:#6f7072;
  --yellow:#f2d35c;
  --red-orange:#ee5a2b;
  --green:#8dc63f;
  --teal:#1d8fb1;
  --magenta:#e5187f;
  --line:#b9bcc2;
}
*{margin:0;padding:0;box-sizing:border-box}
html,body{width:885px;height:1200px;overflow:hidden}
body{background:var(--bg);font-family:"Source Sans 3",Arial,sans-serif;color:var(--text);position:relative}
.page{position:absolute;left:73px;width:755px;background:#fff;overflow:hidden}
.cover{top:44px;height:532px}
.inside{top:641px;height:534px}
.stripe{position:absolute;left:0;bottom:0;width:100%;height:4px;display:flex}
.stripe span{flex:1}
.wordmark{position:absolute;top:30px;font-size:38px;font-weight:400;color:var(--logo-grey);letter-spacing:-.5px;line-height:1}
.band{position:absolute;left:0;top:78px;width:100%;height:308px;background:var(--navy)}
.photo{position:absolute;left:317px;top:84px;width:438px;height:302px;
  clip-path:polygon(24px 0,100% 0,100% 100%,0 100%);
  background:radial-gradient(circle at 58% 55%,#f4f7fb 0,#bcd3ea 25%,#5f86b0 55%,#2c4565 85%)}
.projects{position:absolute;left:14px;top:122px;width:300px;color:#fff}
.projects h2{color:var(--orange);font-size:13px;font-weight:400;margin-bottom:18px}
.projects ul{list-style:none}
.projects li{position:relative;padding-left:14px;font-size:8.4px;font-weight:400;line-height:10px;margin-bottom:10px}
.projects li::before{content:"";position:absolute;left:0;top:2px;width:6px;height:6px;background:var(--orange)}
.contact h2{position:absolute;left:13px;top:420px;font-size:14px;font-weight:400;color:var(--navy)}
.contact-row{position:absolute;left:13px;display:flex;align-items:center;gap:12px;font-size:14px;color:var(--text)}
.contact-row svg{width:20px;height:20px}
.divider{position:absolute;left:187px;top:417px;width:1px;height:78px;background:var(--line)}
.supports{position:absolute;left:204px;top:423px;font-size:7.5px}
.partner{position:absolute;height:20px;border-radius:2px}
.headline{position:absolute;left:430px;top:446px;width:320px;text-align:center;font-size:18px;font-weight:700;line-height:24px;color:var(--navy);letter-spacing:.2px}
.section-band{position:absolute;left:0;top:15px;width:100%;height:44px;background:var(--navy)}
.section-title{position:absolute;top:29px;font-size:17px;font-weight:700;color:#fff;letter-spacing:.3px}
.field-q{position:absolute;left:15px;top:73px;width:350px;font-size:8.6px;line-height:11.5px;color:var(--navy-dark);font-weight:600}
.field-body{position:absolute;left:15px;top:110px;width:350px;font-size:8.6px;line-height:11.5px;text-align:justify}
.map{position:absolute;left:14px;top:200px;width:350px;height:176px;border-radius:40px;
  background:radial-gradient(ellipse at 50% 50%,#9fb0d8 0,#cdd6ee 45%,#ffffff 75%)}
.list{position:absolute;top:403px;font-size:8.6px}
.list h3{font-size:10px;font-weight:400;color:var(--orange);margin-bottom:5px}
.list ul{list-style:none}
.list li{position:relative;padding-left:10px;line-height:11.7px}
.list li::before{content:"";position:absolute;left:0;top:4px;width:4px;height:4px;background:var(--orange)}
.services-intro{position:absolute;left:390px;top:73px;width:349px;font-size:8.6px;line-height:11.5px;text-align:justify;color:var(--navy-dark)}
.connectors{position:absolute;left:0;top:0;width:755px;height:534px}
.service{position:absolute;width:84px;height:59px;border-radius:9px;color:#fff;font-size:6.8px;font-weight:600;text-align:center;line-height:8px;text-transform:uppercase;padding-top:35px;box-shadow:2px 3px 5px rgba(0,0,0,.18)}
.service svg{position:absolute;left:32px;top:8px;width:20px;height:20px}
.service.top{top:146px}
.service.bottom{top:348px;padding-top:38px}
.brand-ring{position:absolute;left:460px;top:237px;width:195px;height:73px;border:3px solid #c3c6cc;border-radius:37px;background:#fff}
.brand-pill{position:absolute;left:472px;top:249px;width:172px;height:53px;border-radius:27px;background:var(--navy);color:#fff;font-size:34px;text-align:center;line-height:50px;letter-spacing:-.5px}
.services-outro{position:absolute;left:405px;top:455px;width:326px;font-size:8.6px;line-height:11.5px;text-align:justify;color:var(--navy-dark)}
</style>
</head>
<body>

<section class="page cover">
  <div class="wordmark" style="left:13px">verdomo</div>
  <div class="wordmark" style="left:393px">verdomo</div>
  <div class="band"></div>
  <div class="photo" role="img" aria-label="Photograph looking up through a glass spiral staircase toward the sky"></div>

  <div class="projects">
    <h2>PROJECTS:</h2>
    <ul>
      <li>Advising Belvant in the elaboration of their donor diversification strategy</li>
      <li>Assisting Ibermark with the review of the intervention guide of Sociaplus and methodological support to conduct policy dialogue at country level (Europe-Latin America)</li>
      <li>Conducting the midterm evaluation of the multi-country programme Corvan (strengthening democratic governance and rule of law in Southeast and Eastern Europe) for the Lowland Rights Council</li>
      <li>Conceptualizing and implementing policy dialogues at country level for the multilateral funded programme Climavera</li>
      <li>Contributing with content, analysis and facilitation to the Harbor Exchange on Cooperation, a multilateral funded multi-stakeholder platform</li>
      <li>Last but not least, contributing to the debate about relevant aspects of the global agenda through different media outlets, universities and think tanks such as El Diario Norte, Geoforum Institute and Instituto Albora.</li>
    </ul>
  </div>

  <div class="contact">
    <h2>CONTACT US</h2>
    <div class="contact-row" style="top:450px">
      <svg viewBox="0 0 20 20"><circle cx="10" cy="10" r="9" fill="none" stroke="var(--orange)" stroke-width="1.6"/><rect x="5" y="6.5" width="10" height="7" fill="none" stroke="var(--orange)" stroke-width="1.3"/><path d="M5 6.5 10 11 15 6.5" fill="none" stroke="var(--orange)" stroke-width="1.3"/></svg>
      <span>info@verdomo.org</span>
    </div>
    <div class="contact-row" style="top:475px">
      <svg viewBox="0 0 20 20"><circle cx="10" cy="10" r="9" fill="none" stroke="var(--orange)" stroke-width="1.6"/><circle cx="10" cy="10" r="5" fill="none" stroke="var(--orange)" stroke-width="1.2"/><path d="M5 10h10M10 5c-2 3-2 7 0 10M10 5c2 3 2 7 0 10" fill="none" stroke="var(--orange)" stroke-width="1"/></svg>
      <span>www.verdomo.org</span>
    </div>
  </div>

  <div class="divider"></div>
  <div class="supports">Verdomo supports the work of:</div>
  <div class="partner" style="left:204px;top:444px;width:34px;background:#2b3f92"></div>
  <div class="partner" style="left:244px;top:446px;width:50px;height:16px;background:#e8d3d6"></div>
  <div class="partner" style="left:300px;top:444px;width:34px;height:18px;background:#cfe0f0"></div>
  <div class="partner" style="left:340px;top:443px;width:20px;border-radius:50%;background:#9ab8d9"></div>
  <div class="partner" style="left:204px;top:472px;width:40px;height:14px;background:#c7d4ea"></div>
  <div class="partner" style="left:250px;top:472px;width:40px;height:14px;background:#f1e0b6"></div>
  <div class="partner" style="left:296px;top:472px;width:40px;height:14px;background:#d2d2d2"></div>
  <div class="partner" style="left:342px;top:469px;width:20px;border-radius:50%;background:#f3c7c2"></div>

  <div class="headline">PROMOTING COLLECTIVE ACTION<br>FOR SUSTAINABLE DEVELOPMENT</div>

  <div class="stripe">
    <span style="background:#26286b"></span><span style="background:#4c9f38"></span><span style="background:#1d8fb1"></span><span style="background:#f29a2e"></span><span style="background:#a21942"></span><span style="background:#fcc30b"></span><span style="background:#e5187f"></span><span style="background:#dd1367"></span><span style="background:#19486a"></span><span style="background:#56c02b"></span><span style="background:#c5192d"></span><span style="background:#26bde2"></span><span style="background:#fd6925"></span><span style="background:#bf8b2e"></span><span style="background:#3f7e44"></span><span style="background:#e5243b"></span>
  </div>
</section>

<section class="page inside">
  <div class="section-band"></div>
  <h2 class="section-title" style="left:15px">OUR FIELD</h2>
  <h2 class="section-title" style="left:389px">OUR SERVICES</h2>

  <p class="field-q">Is it possible to deliver effective solutions in the 21st Century without well-managed collaborative action?</p>
  <p class="field-body">At Verdomo we consider that, both individually and collectively, we are evolving towards more complex and mixed forms of interaction and organization. Our view is that the intellectual effort to understand that evolution needs to be combined with the practical capacity to take advantage of its great potential: the construction of realistic schemes and environments where both citizens and organizations can participate critically and contribute effectively to the public good.</p>

  <div class="map" role="img" aria-label="Dotted world map with pins marking countries where Verdomo has worked"></div>

  <div class="list" style="left:13px">
    <h3>We specialize in:</h3>
    <ul>
      <li>Policy dialogue</li>
      <li>Donor diversification strategies</li>
      <li>Multi-stakeholder partnerships</li>
      <li>Strategic partnerships</li>
      <li>Coalition building</li>
      <li>Goal-directed networks</li>
    </ul>
  </div>
  <div class="list" style="left:209px">
    <h3>We work with:</h3>
    <ul>
      <li>International Organizations</li>
      <li>NGOs</li>
      <li>Development agencies</li>
      <li>Trade unions</li>
      <li>Regional and Local governments</li>
      <li>Private sector</li>
      <li>Universities and Think tanks</li>
    </ul>
  </div>

  <p class="services-intro">Verdomo is a response to the growing need of a wide array of organizations to understand changes in the development landscape, undergo structural changes, improve processes and increase the impact of their participation in collective actions to attain development goals.</p>

  <svg class="connectors" viewBox="0 0 755 534" aria-hidden="true">
    <g fill="none" stroke="#c3c6cc" stroke-width="2">
      <path d="M455 213V223H538V238"/>
      <path d="M563 213V238"/>
      <path d="M654 213V223H588V238"/>
      <path d="M538 310V325H455V340"/>
      <path d="M563 310V340"/>
      <path d="M588 310V325H654V340"/>
    </g>
    <circle cx="455" cy="213" r="2.5" fill="var(--yellow)"/><circle cx="538" cy="236" r="2.5" fill="var(--yellow)"/>
    <circle cx="563" cy="213" r="2.5" fill="var(--red-orange)"/><circle cx="563" cy="236" r="2.5" fill="var(--red-orange)"/>
    <circle cx="654" cy="213" r="2.5" fill="var(--green)"/><circle cx="588" cy="236" r="2.5" fill="var(--green)"/>
    <circle cx="538" cy="312" r="2.5" fill="var(--teal)"/><circle cx="455" cy="340" r="2.5" fill="var(--teal)"/>
    <circle cx="563" cy="312" r="2.5" fill="var(--magenta)"/><circle cx="563" cy="340" r="2.5" fill="var(--magenta)"/>
    <circle cx="588" cy="312" r="2.5" fill="var(--navy-dark)"/><circle cx="654" cy="340" r="2.5" fill="var(--navy-dark)"/>
  </svg>

  <div class="service top" style="left:413px;background:var(--yellow)">
    <svg viewBox="0 0 20 20"><circle cx="10" cy="10" r="8" fill="none" stroke="#fff" stroke-width="1.6"/><circle cx="10" cy="10" r="4" fill="none" stroke="#fff" stroke-width="1.6"/><circle cx="10" cy="10" r="1.3" fill="#fff"/></svg>
    Research and<br>analysis
  </div>
  <div class="service top" style="left:521px;background:var(--red-orange)">
    <svg viewBox="0 0 20 20" fill="#fff"><circle cx="5" cy="7" r="2.3"/><circle cx="10" cy="5.5" r="2.6"/><circle cx="15" cy="7" r="2.3"/><path d="M1 16c0-4 8-4 8 0zM11 16c0-4 8-4 8 0zM5.5 15c0-5 9-5 9 0z"/></svg>
    Facilitation and<br>training
  </div>
  <div class="service top" style="left:612px;background:var(--green)">
    <svg viewBox="0 0 20 20" fill="none" stroke="#fff" stroke-width="1.8"><circle cx="7" cy="12" r="4"/><circle cx="14" cy="5.5" r="3"/></svg>
    Knowledge<br>management
  </div>

  <div class="brand-ring"></div>
  <div class="brand-pill">verdomo</div>

  <div class="service bottom" style="left:413px;background:var(--teal)">
    <svg viewBox="0 0 20 20"><circle cx="10" cy="10" r="8.5" fill="#fff"/><circle cx="10" cy="10" r="2.5" fill="var(--teal)"/><path d="M10 2v5M3 14l4.5-2.5M17 14l-4.5-2.5" stroke="var(--teal)" stroke-width="2"/></svg>
    Coalition building
  </div>
  <div class="service bottom" style="left:521px;background:var(--magenta)">
    <svg viewBox="0 0 20 20" fill="none" stroke="#fff" stroke-width="1.5"><rect x="3" y="4" width="14" height="9"/><path d="M1 16h18"/><path d="M6 11l3-3 2 2 3-4" /></svg>
    Evaluation
  </div>
  <div class="service bottom" style="left:612px;background:var(--navy-dark)">
    <svg viewBox="0 0 20 20" fill="none" stroke="#fff" stroke-width="1.5"><circle cx="10" cy="10" r="3"/><circle cx="10" cy="2.8" r="1.8"/><circle cx="10" cy="17.2" r="1.8"/><circle cx="2.8" cy="10" r="1.8"/><circle cx="17.2" cy="10" r="1.8"/><path d="M10 4.6V7M10 13v2.4M4.6 10H7M13 10h2.4"/></svg>
    Communication
  </div>

  <p class="services-outro">At Verdomo we believe that theory cannot be separated from practice. We provide the necessary tools, methods and skills for public institutions, business and civil society organizations to operate effectively in multi-actor complex environments, whether as part of their internal management process or in the context of their relations with other actors.</p>

  <div class="stripe">
    <span style="background:#26286b"></span><span style="background:#4c9f38"></span><span style="background:#1d8fb1"></span><span style="background:#f29a2e"></span><span style="background:#a21942"></span><span style="background:#fcc30b"></span><span style="background:#e5187f"></span><span style="background:#dd1367"></span><span style="background:#19486a"></span><span style="background:#56c02b"></span><span style="background:#c5192d"></span><span style="background:#26bde2"></span><span style="background:#fd6925"></span><span style="background:#bf8b2e"></span><span style="background:#3f7e44"></span><span style="background:#e5243b"></span>
  </div>
</section>

</body>
</html>
```